Plakat für Hersteller von maßgefertigten Tischunikaten aus Massivholz
Zielgruppe
Wir sind einen Firma die sich auf die Fertigung von maßgefertigten Tischunikaten aus Massivholz spezialisiert hat. Unsere Zielgruppe sind Design affine Leute, im Alter von 35-55 Jahren
Aufgabenstellung
Wir benötigen das Design für eine Messewand mit den Maßen 443X227 cm. 5 Zentimeter rundlaufen dürfen keine Elemente mehr platziert werden. Die Messewand steht im Hintergrund von unserem Stand bei verschiedenen Designmessen
Infos die auf die Messewand müssen: Logo, Tischmanufaktur aus Stuttgart, Maßgefertigte Tischunikate (Bei der Formulierung bin ich flexibel, ihr könnt bspw. auch nur Stichworte benutzen, aber Stuttgart und maßgefertigt ist wichtig).
Die Messewand soll sehr minimalistisch gestaltet sein, bei der letzten Messewand hatten wir ein Foto von einem Tisch im Hintergrund und das sah merkwürdig aus.

```html
<!DOCTYPE html>
<html lang="de">
<head>
<meta charset="utf-8">
<title>Lindqvist Manufaktur – Messewand</title>
<link rel="stylesheet" href="https://fonts.googleapis.com/css2?family=Josefin+Sans:wght@200;300;600&display=swap">
<style>
  :root {
    --page-bg: #e6e6e6;
    --wall-dark: #222222;
    --wall-mid: #2e2e2e;
    --wall-light: #575757;
    --text-white: #ffffff;
    --accent-yellow: #f6dc4c;
    --accent-gold: #f2c94c;
    --placeholder-a: #242424;
    --placeholder-b: #2b2b2b;
  }
  * { margin: 0; padding: 0; box-sizing: border-box; }
  html, body {
    width: 1200px;
    height: 816px;
    overflow: hidden;
    background: var(--page-bg);
  }
  .trade-wall {
    position: absolute;
    left: 0;
    top: 101px;
    width: 1200px;
    height: 614px;
    overflow: hidden;
    background:
      radial-gradient(ellipse 620px 480px at 0 0, var(--wall-light) 0%, var(--wall-mid) 45%, transparent 80%),
      var(--wall-dark);
    font-family: "Josefin Sans", sans-serif;
    color: var(--text-white);
  }
  .headline {
    position: absolute;
    left: 74px;
    top: 60px;
    font-weight: 200;
    font-size: 63px;
    line-height: 82px;
    letter-spacing: -0.015em;
    text-transform: uppercase;
    white-space: nowrap;
  }
  .headline .city {
    background: linear-gradient(90deg, var(--accent-gold), var(--accent-yellow));
    -webkit-background-clip: text;
    background-clip: text;
    color: transparent;
  }
  .brand {
    position: absolute;
    left: 895px;
    top: 55px;
    display: flex;
    align-items: center;
    gap: 11px;
  }
  .brand-circle {
    width: 67px;
    height: 67px;
    border: 4px solid var(--text-white);
    border-radius: 50%;
  }
  .brand-name {
    font-weight: 600;
    font-size: 25px;
    line-height: 28px;
    letter-spacing: 0.01em;
  }
  .website {
    position: absolute;
    left: 74px;
    top: 518px;
    font-weight: 300;
    font-size: 25px;
    letter-spacing: 0.005em;
  }
  .table-drawing {
    position: absolute;
    left: 689px;
    top: 264px;
    width: 511px;
    height: 350px;
    background: linear-gradient(180deg, var(--placeholder-b) 0%, var(--placeholder-a) 100%);
  }
</style>
</head>
<body>
  <section class="trade-wall">
    <h1 class="headline">
      Maßgefertigte<br>
      Tischunikate.<br>
      Tischmanufaktur<br>
      aus <span class="city">Stuttgart.</span>
    </h1>

    <div class="brand">
      <span class="brand-circle" aria-hidden="true"></span>
      <span class="brand-name">Lindqvist<br>Manufaktur</span>
    </div>

    <p class="website">www.lindqvist-manufaktur.de</p>

    <div class="table-drawing" role="img" aria-label="Feine weiße Linienzeichnung eines Massivholztisches"></div>
  </section>
</body>
</html>
```